WordPress webdesign with coding for our company BRISK The Answer

BRISK The Answer is a payrolling company such as Montaval Wages (one of our competitor https://www.montaval-wages.ch/fr/). We need to set up our website in both languages (Fr and Eng). Our logo is enclosed.
we would like something simple explaining what is payrolling in Graph and wording, who we are and a contact page. you can also take some example if needed from our mother company BRISK The Horizon (www.briskthehorizon.ch) or our sister company (www.briskyourstride.ch). we would like to keep the color panel of our logo (ref. Black = PANTONE P Process Black C
Pink = PANTONE P Process Magenta C
Grey = PANTONE 430 C) as the driver of the website.

```html
<!DOCTYPE html>
<html lang="en">
<head>
<meta charset="utf-8">
<title>BRISK The Answer – Payrolling</title>
<link href="https://fonts.googleapis.com/css2?family=Poppins:wght@300;400;500;600;700&display=swap" rel="stylesheet">
<style>
:root{
  --magenta:#e4087e;
  --magenta-soft:#f7c6e0;
  --ink:#1d1b1c;
  --ink-2:#3b3a3b;
  --grey:#7c868d;
  --text:#4a4a4a;
  --line:#e2e2e2;
  --paper:#ffffff;
  --mist:#f2f2f2;
}
*{box-sizing:border-box;margin:0;padding:0}
html,body{width:1200px;height:5254px;overflow:hidden}
body{font-family:"Poppins",sans-serif;color:var(--ink);background:var(--paper);position:relative}
section,header,footer{position:relative;width:1200px;overflow:hidden}
.abs{position:absolute}
.btn{position:absolute;display:flex;align-items:center;justify-content:center;background:var(--magenta);color:#fff;font-size:12px;font-weight:600;border-radius:22px;letter-spacing:.3px}
.accent-bar{position:absolute;width:44px;height:4px;border-radius:2px;background:var(--magenta)}
.sec-title{position:absolute;left:0;width:1200px;text-align:center;font-weight:600;font-size:35px;text-transform:uppercase;letter-spacing:.5px}
.sec-title .light{font-weight:500;color:var(--ink-2)}

/* header */
.site-header{height:98px}
.logo{position:absolute;left:143px;top:33px;font-size:24px;font-weight:700;letter-spacing:1px;color:var(--ink)}
.nav{position:absolute;top:40px;left:455px;display:flex;gap:26px;font-size:13px;color:var(--ink-2)}
.nav .active{color:var(--magenta);font-weight:500}
.header-tools{position:absolute;top:36px;left:925px;display:flex;gap:22px;align-items:center;font-size:13px}
.header-rule{position:absolute;left:88px;right:88px;bottom:2px;height:1px;background:var(--line)}

/* hero */
.hero{height:567px;background:radial-gradient(circle at 0% 0%,#fbd9ea 0,rgba(255,255,255,0) 320px),radial-gradient(circle at 100% 80%,#fbe1ee 0,rgba(255,255,255,0) 300px),#fff}
.hero h1{position:absolute;left:141px;top:108px;font-size:40px;font-weight:600;line-height:58px;text-transform:uppercase}
.hero .lead{position:absolute;left:143px;top:228px;width:420px;font-size:16px;line-height:27px;color:var(--text)}
.clients{position:absolute;left:150px;top:412px;display:flex;align-items:center}
.clients .dot{width:44px;height:44px;border-radius:50%;border:2px solid #fff;margin-right:-12px;background:linear-gradient(135deg,#b5835c,#5a3a2c)}
.clients .count{margin-left:26px}
.clients strong{display:block;font-size:20px;font-weight:600}
.clients span{font-size:13px;color:var(--text)}
.hero-disc{position:absolute;left:700px;top:138px;width:360px;height:360px;border-radius:50%;background:var(--magenta)}
.hero-person{position:absolute;left:790px;top:24px;width:250px;height:500px;border-radius:120px 120px 0 0;background:linear-gradient(180deg,#6d5a52 0,#3a3a3c 40%,#59595c 100%)}
.card{position:absolute;background:#fff;border-radius:8px;box-shadow:0 6px 24px rgba(0,0,0,.14);font-size:7px;color:var(--text)}
.pay-summary{left:590px;top:335px;width:234px;height:180px;padding:14px 16px}
.pay-summary h4{font-size:10px;font-weight:600;color:var(--ink)}
.pay-summary .chip{position:absolute;left:68px;top:36px;width:30px;height:9px;border-radius:5px;background:#4cc15b}
.pay-summary table{position:absolute;left:16px;top:60px;width:200px;border-collapse:collapse}
.pay-summary td{padding:2px 0;font-size:6px}
.pay-summary .foot{position:absolute;left:16px;bottom:14px;display:flex;gap:30px;font-size:6px;font-weight:600;color:var(--ink)}
.pay-summary .go{position:absolute;right:20px;bottom:11px;width:38px;height:14px;border-radius:3px;background:#3a6ee8}
.payrolls{left:934px;top:45px;width:137px;height:112px;padding:10px}
.payrolls h5{font-size:7px;font-weight:600;color:var(--ink);margin-bottom:10px}
.payrolls li{list-style:none;display:flex;align-items:center;gap:5px;margin-bottom:11px;font-size:6px}
.payrolls li i{width:11px;height:11px;border-radius:50%;background:#d9b8a5}
.payrolls li b{margin-left:auto;font-weight:500}

/* services */
.services{height:600px;background:var(--ink);color:#fff}
.services .sec-title{top:108px;color:#fff}
.service{position:absolute;top:200px;width:290px;text-align:center}
.service .orb{width:172px;height:172px;border-radius:50%;margin:0 auto;display:flex;align-items:center;justify-content:center;background:radial-gradient(circle at 70% 70%,#f6c5de,#ffffff 70%);border:8px solid #fff;box-shadow:inset 0 0 0 12px var(--ink)}
.service .orb.pink{background:radial-gradient(circle at 40% 35%,#ff6cb8,var(--magenta) 70%);border-color:#f5a5cf;box-shadow:none}
.service h3{margin-top:30px;font-size:15px;font-weight:500;letter-spacing:.5px}
.service p{margin-top:10px;font-size:12.5px;line-height:25px;color:#ddd}

/* partner */
.partner{height:694px;background:radial-gradient(circle at 0% 25%,#fbd3e7 0,rgba(255,255,255,0) 260px),#fff}
.partner .l1{top:125px}
.partner .l2{top:176px;font-weight:500;color:var(--ink-2)}
.pcard{position:absolute;top:296px;width:253px;height:296px;background:#fff;box-shadow:0 4px 18px rgba(0,0,0,.08);padding:74px 24px 0}
.pcard .diamond{position:absolute;left:94px;top:-46px;width:66px;height:66px;transform:rotate(45deg);background:var(--ink-2);display:flex;align-items:center;justify-content:center}
.pcard .diamond.pink{background:var(--magenta)}
.pcard .diamond svg{transform:rotate(-45deg)}
.pcard h4{font-size:12.5px;font-weight:600;line-height:22px;text-transform:uppercase;min-height:44px}
.pcard li{list-style:none;position:relative;padding-left:16px;font-size:12px;line-height:22px;color:var(--text);margin-top:14px}
.pcard li::before{content:"";position:absolute;left:0;top:6px;width:8px;height:4px;border-left:2px solid var(--magenta);border-bottom:2px solid var(--magenta);transform:rotate(-45deg)}

/* solution */
.solution{height:649px;background:linear-gradient(90deg,#e4e4e6 0,#f0f0f1 55%,#f4f4f4 100%)}
.solution-photo{position:absolute;left:612px;top:0;width:588px;height:649px;background:linear-gradient(160deg,#cfd6c8 0,#e8ece6 35%,#f2f2f2 60%,#c7c9cc 100%)}
.solution h2{position:absolute;left:141px;top:146px;font-size:35px;font-weight:600;text-transform:uppercase}
.solution h2 span{font-weight:500;color:var(--ink-2)}
.body-copy{font-size:12.5px;line-height:25.7px;color:var(--text)}
.solution .body-copy{position:absolute;left:141px;width:430px}

/* what is payrolling */
.what{height:657px;background:radial-gradient(circle at 100% 0%,#fbd7ea 0,rgba(255,255,255,0) 260px),radial-gradient(circle at 0% 100%,#fbd3e7 0,rgba(255,255,255,0) 200px),#fff}
.what .label{position:absolute;font-size:12.5px;font-weight:500}
.what h2{position:absolute;left:639px;top:126px;font-size:35px;font-weight:600;text-transform:uppercase}
.what .body-copy{position:absolute;left:639px;width:425px}

/* why */
.why{height:540px;background:#fff}
.why .sec-title{top:76px}
.pillar{position:absolute;top:189px;width:266px;height:266px;border-radius:50%;background:var(--ink-2);color:#fff;text-align:center;padding-top:40px}
.pillar.pink{background:var(--magenta)}
.pillar h3{margin-top:10px;font-size:14px;font-weight:600;text-transform:uppercase}
.pillar hr{width:40px;border:0;border-top:2px solid #fff;margin:10px auto}
.pillar p{width:160px;margin:0 auto;font-size:11.5px;line-height:22px;color:#eee}
.pillar-arc{position:absolute;top:173px;width:298px;height:298px}

/* testimonials */
.testimonials{height:555px;background:var(--mist)}
.testimonials .sec-title{top:137px}
.avatar{position:absolute;left:561px;top:211px;width:78px;height:78px;border-radius:50%;background:radial-gradient(circle at 50% 40%,#d98b5f,#e9a27c 60%,#f0b592)}
.quote{position:absolute;left:280px;top:298px;width:640px;text-align:center;font-size:12.5px;line-height:26px;color:var(--text)}
.who{position:absolute;left:0;width:1175px;text-align:center;top:449px;font-size:13px;font-weight:500}
.role{position:absolute;left:0;width:1175px;text-align:center;top:473px;font-size:13.5px;font-weight:500;color:var(--magenta)}
.arrow{position:absolute;top:290px;width:58px;height:58px;border-radius:50%;background:#fff;box-shadow:0 2px 10px rgba(0,0,0,.08);display:flex;align-items:center;justify-content:center}

/* cta */
.cta{height:465px;background:var(--magenta);color:#fff;text-align:center}
.cta h2{position:absolute;left:0;width:1200px;top:110px;font-size:35px;font-weight:600;line-height:51px;text-transform:uppercase}
.cta p{position:absolute;left:240px;width:720px;top:232px;font-size:15px;line-height:28px}
.cta .btn{left:467px;top:325px;width:265px;height:40px;background:var(--ink);font-size:13px}

/* footer */
.site-footer{height:429px;background:var(--ink);color:#fff}
.site-footer .logo{left:150px;top:98px;color:#fff;font-size:22px;line-height:28px;letter-spacing:1px}
.social{position:absolute;left:147px;top:176px;display:flex;gap:8px}
.social span{width:36px;height:36px;border-radius:50%;background:#fff}
.fcol{position:absolute;top:90px}
.fcol h6{font-size:14px;font-weight:500;color:var(--magenta);margin-bottom:8px}
.fcol li{list-style:none;font-size:13px;line-height:25.5px}
.footer-rule{position:absolute;left:0;right:0;top:269px;height:1px;background:#3a3839}
.copyright{position:absolute;left:0;width:1200px;text-align:center;top:306px;font-size:12px}
</style>
</head>
<body>

<header class="site-header">
  <div class="logo">BRISK THE ANSWER</div>
  <nav class="nav">
    <span class="active">Home</span><span>About Us</span><span>What Is Payrolling?</span><span>Agency</span><span>Blog</span>
  </nav>
  <div class="header-tools">
    <svg width="16" height="16" viewBox="0 0 16 16" fill="none" stroke="#1d1b1c" stroke-width="1.5"><circle cx="8" cy="5" r="3"/><path d="M2 15c0-3.5 3-5 6-5s6 1.5 6 5"/></svg>
    <svg width="18" height="14" viewBox="0 0 18 14" fill="none" stroke="#1d1b1c" stroke-width="1.5"><rect x="1" y="1" width="16" height="12" rx="2"/><path d="M1 2l8 6 8-6"/></svg>
    <span>EN ⌄</span>
  </div>
  <div class="header-rule"></div>
</header>

<section class="hero">
  <h1>The smart way to<br>work independently.</h1>
  <p class="lead">We simplify payrolling so you can deliver your expertise with confidence.</p>
  <div class="btn" style="left:141px;top:325px;width:214px;height:44px">DISCOVER PAYROLLING</div>
  <div class="clients">
    <span class="dot"></span><span class="dot"></span><span class="dot"></span>
    <div class="count"><strong>500+</strong><span>Corporate Clients</span></div>
  </div>
  <div class="hero-disc"></div>
  <div class="hero-person" role="img" aria-label="Photo of a smiling professional holding a laptop"></div>
  <div class="card pay-summary">
    <h4>Payroll Summary</h4>
    <span class="chip"></span>
    <table>
      <tr><td>Employee</td><td>142</td><td>Pay period</td><td>Month</td></tr>
      <tr><td>Base pay</td><td>$ 320</td><td>Social cost</td><td>$ 180</td></tr>
      <tr><td>Overtime</td><td>$ 40</td><td>Pension</td><td>$ 60</td></tr>
      <tr><td>Bonus</td><td>$ 1,750</td><td>Deduction</td><td>$ 1,200</td></tr>
      <tr><td>Other</td><td>$ 2,600</td><td></td><td></td></tr>
    </table>
    <div class="foot"><span>Gross Wage $ 5,000</span><span>Net Pay</span></div>
    <span class="go"></span>
  </div>
  <div class="card payrolls">
    <h5>Payrolls</h5>
    <ul>
      <li><i></i>Lena Morel<b>$2000</b></li>
      <li><i></i>Tom Berger<b>$2000</b></li>
      <li><i></i>Ines Rochat<b>$2000</b></li>
    </ul>
  </div>
</section>

<section class="services">
  <span class="accent-bar" style="left:578px;top:80px"></span>
  <h2 class="sec-title" style="top:108px">Discover all our services</h2>
  <div class="service" style="left:153px">
    <div class="orb"><svg width="60" height="60" viewBox="0 0 60 60" fill="none" stroke="#e4087e" stroke-width="3"><circle cx="30" cy="26" r="16"/><path d="M30 17v18M25 21h8a3 3 0 010 6h-6a3 3 0 000 6h8"/><path d="M8 50h44"/></svg></div>
    <h3>PAYROLLING</h3>
    <p>Work with the best experts quickly, in Switzerland and internationally.</p>
  </div>
  <div class="service" style="left:473px">
    <div class="orb pink"><svg width="60" height="60" viewBox="0 0 60 60" fill="none" stroke="#fff" stroke-width="3"><rect x="14" y="8" width="28" height="38" rx="3"/><path d="M20 18h16M20 26h16M20 34h10"/><circle cx="42" cy="42" r="9"/></svg></div>
    <h3>SOURCING</h3>
    <p>Find the best talent to move your business forward.</p>
  </div>
  <div class="service" style="left:792px;top:208px">
    <div class="orb"><svg width="60" height="60" viewBox="0 0 60 60" fill="none" stroke="#e4087e" stroke-width="3"><rect x="16" y="22" width="28" height="28"/><path d="M22 30h4M34 30h4M22 40h4M34 40h4"/><circle cx="44" cy="14" r="7"/></svg></div>
    <h3>PAYROLL OUT SOURCE</h3>
    <p>Outsource your employee payroll management in full compliance.</p>
  </div>
</section>

<section class="partner">
  <span class="accent-bar" style="left:578px;top:84px"></span>
  <h2 class="sec-title l1">Working with BRISK The Answer</h2>
  <h2 class="sec-title l2">Means working with a partner</h2>
  <div class="pcard" style="left:94px">
    <div class="diamond"><svg width="34" height="34" viewBox="0 0 34 34" fill="none" stroke="#fff" stroke-width="2"><circle cx="17" cy="10" r="4"/><circle cx="8" cy="16" r="3"/><circle cx="26" cy="16" r="3"/><path d="M9 28c0-5 4-8 8-8s8 3 8 8"/></svg></div>
    <h4>Market leadership<br>&amp; reliability</h4>
    <ul><li>Market leader in Swiss payrolling.</li><li>Proven financial stability and a solid infrastructure to support professionals and companies.</li></ul>
  </div>
  <div class="pcard" style="left:347px">
    <div class="diamond"><svg width="34" height="34" viewBox="0 0 34 34" fill="none" stroke="#fff" stroke-width="2"><rect x="8" y="5" width="18" height="25" rx="2"/><path d="M12 13h10M12 19h10M12 25h6"/></svg></div>
    <h4>Our compliance &amp;<br>certification</h4>
    <ul><li>Market leader in Swiss payrolling.</li><li>Proven financial stability and a solid infrastructure to support professionals and companies.</li></ul>
  </div>
  <div class="pcard" style="left:600px">
    <div class="diamond pink"><svg width="34" height="34" viewBox="0 0 34 34" fill="none" stroke="#fff" stroke-width="2"><circle cx="17" cy="17" r="11"/><circle cx="17" cy="17" r="5"/></svg></div>
    <h4>Agility &amp; responsiveness</h4>
    <ul><li>Market leader in Swiss payrolling.</li><li>Proven financial stability and a solid infrastructure to support professionals and companies.</li></ul>
  </div>
  <div class="pcard" style="left:853px">
    <div class="diamond"><svg width="34" height="34" viewBox="0 0 34 34" fill="none" stroke="#fff" stroke-width="2"><circle cx="17" cy="15" r="7"/><path d="M17 22v8M5 8l5 3M29 8l-5 3M5 24l5-3M29 24l-5-3"/></svg></div>
    <h4>Digital first approach</h4>
    <ul><li>Market leader in Swiss payrolling.</li><li>Proven financial stability and a solid infrastructure to support professionals and companies.</li></ul>
  </div>
</section>

<section class="solution">
  <div class="solution-photo" role="img" aria-label="Photo of a relaxed senior professional smiling at his laptop in a bright office"></div>
  <span class="accent-bar" style="left:143px;top:118px"></span>
  <h2>BRISK Payroll <span>Solution</span></h2>
  <p class="body-copy" style="top:222px">Lorem ipsum dolor sit amet, consectetur adipiscing elit, sed do eiusmod tempor incididunt ut labore et dolore magna aliqua. Ut enim ad minim veniam, quis nostrud exercitation ullamco laboris nisi ut aliquip ex ea commodo consequat. Duis aute irure dolor in reprehenderit in voluptate velit esse cillum dolore eu fugiat nulla pariatur. Excepteur sint occaecat cupidatat non proident, sunt in culpa qui officia deserunt mollit anim id est laborum.</p>
  <p class="body-copy" style="top:412px">Lorem ipsum dolor sit amet, consectetur adipiscing elit, sed do eiusmod tempor incididunt ut labore et dolore magna aliqua. Ut enim ad minim veniam, quis nostrud</p>
  <div class="btn" style="left:143px;top:515px;width:214px;height:42px">DISCOVER PAYROLLING</div>
</section>

<section class="what">
  <svg class="abs" style="left:170px;top:150px" width="380" height="330" viewBox="0 0 380 330">
    <circle cx="187" cy="200" r="155" fill="none" stroke="#bbb" stroke-width="1.5"/>
    <circle cx="187" cy="200" r="142" fill="none" stroke="#d6d6d6" stroke-width="1"/>
    <circle cx="187" cy="200" r="46" fill="#fbe1ee"/>
    <circle cx="187" cy="45" r="26" fill="#3b3a3b" stroke="#fff" stroke-width="4"/>
    <rect x="176" y="34" width="22" height="22" rx="2" fill="none" stroke="#fff" stroke-width="2"/>
    <circle cx="63" cy="267" r="26" fill="#1d1b1c" stroke="#fff" stroke-width="4"/>
    <circle cx="63" cy="267" r="10" fill="none" stroke="#fff" stroke-width="2"/>
    <circle cx="308" cy="264" r="26" fill="#e4087e" stroke="#fff" stroke-width="4"/>
    <circle cx="308" cy="264" r="10" fill="none" stroke="#fff" stroke-width="2"/>
  </svg>
  <span class="label" style="left:267px;top:130px">The Consultant/Freelancer</span>
  <span class="label" style="left:117px;top:444px">The Payrolling Company</span>
  <span class="label" style="left:432px;top:438px">The Client Company</span>
  <span class="accent-bar" style="left:639px;top:98px"></span>
  <h2>What is <span style="font-weight:500;color:var(--ink-2)">Payrolling</span></h2>
  <p class="body-copy" style="top:200px">Lorem ipsum dolor sit amet, consectetur adipiscing elit, sed do eiusmod tempor incididunt ut labore et dolore magna aliqua. Ut enim ad minim veniam, quis nostrud exercitation ullamco laboris nisi ut aliquip ex ea commodo consequat. Duis aute irure dolor in reprehenderit in voluptate velit esse cillum dolore eu fugiat nulla pariatur. Excepteur sint occaecat cupidatat non proident, sunt in culpa qui officia deserunt mollit anim id est laborum.</p>
  <p class="body-copy" style="top:390px">Lorem ipsum dolor sit amet, consectetur adipiscing elit, sed do eiusmod tempor incididunt ut labore et dolore magna aliqua. Ut enim ad minim veniam, quis nostrud</p>
  <div class="btn" style="left:639px;top:498px;width:152px;height:42px">View More</div>
</section>

<section class="why">
  <span class="accent-bar" style="left:578px;top:42px"></span>
  <h2 class="sec-title">Why <span class="light">choose us</span></h2>
  <svg class="pillar-arc" style="left:157px" viewBox="0 0 298 298"><path d="M149 2A147 147 0 0 0 149 296" fill="none" stroke="#555" stroke-width="1.5"/></svg>
  <svg class="pillar-arc" style="left:449px" viewBox="0 0 298 298"><path d="M10 200A147 147 0 0 0 288 200" fill="none" stroke="#555" stroke-width="1.5"/></svg>
  <svg class="pillar-arc" style="left:741px" viewBox="0 0 298 298"><path d="M149 2A147 147 0 0 1 296 149" fill="none" stroke="#555" stroke-width="1.5"/><circle cx="296" cy="149" r="4" fill="#555"/></svg>
  <div class="pillar" style="left:173px">
    <svg width="56" height="50" viewBox="0 0 56 50" fill="none" stroke="#fff" stroke-width="2.5"><path d="M22 44V18a4 4 0 018 0v12l10 2a5 5 0 014 6l-2 6"/><path d="M16 14a12 12 0 0120 0"/></svg>
    <h3>Management</h3><hr>
    <p>Sed ut perspiciatis unde omnis iste natus error sit voluptatem accu</p>
  </div>
  <div class="pillar pink" style="left:465px">
    <svg width="56" height="50" viewBox="0 0 56 50" fill="none" stroke="#fff" stroke-width="2.5"><circle cx="28" cy="14" r="8"/><path d="M28 4V2M18 8l-2-2M38 8l2-2M24 24v20h8V24"/></svg>
    <h3>Expertise</h3><hr>
    <p>Sed ut perspiciatis unde omnis iste natus error sit voluptatem accu</p>
  </div>
  <div class="pillar" style="left:757px">
    <svg width="56" height="50" viewBox="0 0 56 50" fill="none" stroke="#fff" stroke-width="2.5"><path d="M16 44V34c-5-4-7-9-6-15 2-10 11-15 20-13 9 2 14 10 12 19l-2 2 2 5h-4v6h-8v6"/><path d="M30 14l-4 8h6l-4 8"/></svg>
    <h3>Accompaniement</h3><hr>
    <p>Sed ut perspiciatis unde omnis iste natus error sit voluptatem accusantium dolo</p>
  </div>
</section>

<section class="testimonials">
  <span class="accent-bar" style="left:578px;top:106px"></span>
  <h2 class="sec-title">Our <span class="light">testimonials</span></h2>
  <div class="avatar" role="img" aria-label="Portrait photo of the client"></div>
  <p class="quote">Sed ut perspiciatis unde omnis iste natus error sit voluptatem accusantium doloremque laudantium, totam rem aperiam, eaque ipsa quae ab illo inventore veritatis et quasi architecto beatae vitae dicta sunt explicabo. Nemo enim ipsam voluptatem quia voluptas sit aspernatur aut odit aut fugit, sed quia consequuntur magni dolores eos qui ratione vo</p>
  <div class="who">MARCO DELVAL</div>
  <div class="role">Project Manager</div>
  <div class="arrow" style="left:63px"><svg width="12" height="16" viewBox="0 0 12 16"><path d="M9 2L3 8l6 6" fill="none" stroke="#1d1b1c" stroke-width="2"/></svg></div>
  <div class="arrow" style="left:1077px"><svg width="12" height="16" viewBox="0 0 12 16"><path d="M3 2l6 6-6 6" fill="none" stroke="#1d1b1c" stroke-width="2"/></svg></div>
</section>

<section class="cta">
  <h2>Are you looking for a trusted partner<br>to support you in your need for freedom?</h2>
  <p>We simplify payrolling by handling contracts, payroll, and administration, giving you the flexibility to focus fully on your projects.</p>
  <div class="btn">Start Your Payrolling Journey</div>
</section>

<footer class="site-footer">
  <div class="logo">BRISK<br>THE ANSWER</div>
  <div class="social"><span></span><span></span><span></span></div>
  <div class="fcol" style="left:414px"><h6>Consultant</h6><ul><li>How payrolling works</li><li>Our payrolling offer</li><li>Frequently Asked</li><li>Questions</li></ul></div>
  <div class="fcol" style="left:661px"><h6>Business</h6><ul><li>External talent management</li><li>Payroll Outsourcing</li><li>Talent sourcing</li><li>Are you an agency?</li></ul></div>
  <div class="fcol" style="left:963px"><h6>About</h6><ul><li>Who are we ?</li><li>Contact us</li></ul></div>
  <div class="footer-rule"></div>
  <div class="copyright">Copyright@2025.All Rights Reserved</div>
</footer>

</body>
</html>
```